Banner to be displayed at local Farmers Market Booth.

Graphic Design Brief: Farmers Market Banner Contest

Project Overview:We are seeking talented graphic designers to create a visually appealing banner for our booth at the local farmers market. Our company specializes in healthy, all-natural dog and cat treats, and we want a banner that captures our brand identity while drawing in pet owners who value quality and nutrition for their furry friends.

Banner Specifications:

Size: 24 inches x 60 inches (Horizontal orientation) 24" High X 60 wide

Theme: Vintage/Retro

Style: Warm, inviting, nostalgic with a touch of rustic charm

Colors: Earthy, muted tones such as warm browns, soft greens, and creamy yellows. Pops of red or blue may be used sparingly for accents. OR Black and White with gray scales. Would like to see both

Typography: Retro-style fonts that are readable and align with the vintage aesthetic.

Key Elements to Include: website (www.moltbyfarms.com)

Company Name: Moltby Farms

Tagline: " Simply Honest Bites "
Imagery: Illustrations or stylized graphics of happy dogs and cats, possibly interacting with treats.

Emphasis on Natural Ingredients: Icons or design elements that subtly suggest freshness and quality (e.g., leaves, wheat, bones, or paw prints).

Farmers Market Appeal: A design that blends well with the artisanal, handmade, and farm-fresh atmosphere of the market.

Design Considerations:

The banner should be easily readable from a distance.

A balanced composition that doesn't feel overcrowded.

Should evoke trust and warmth while maintaining a professional look.

Avoid overly modern or sleek elements that don’t align with the vintage aesthetic.

Submission Requirements:

High-resolution digital file in PDF or AI format.

CMYK color mode for printing purposes.

Must include a mockup or preview of how it would look in a real farmers market setting.

We look forward to seeing your creative interpretations of our brand! If you have any questions, feel free to reach out.

Font styles to use
Other font styles liked:
• See attachement

Requirements
Nice to have
• Retro/Vintage,playful BUT NOT whimsical

```html
<!DOCTYPE html>
<html lang="en">
<head>
<meta charset="utf-8">
<title>Moltby Farms – Market Banner</title>
<link rel="stylesheet" href="https://fonts.googleapis.com/css2?family=Archivo:wdth,wght@125,900&family=EB+Garamond:wght@500;700&display=swap">
<style>
  :root {
    --page: #e9e9e6;
    --cream: #f1efe9;
    --ink: #141414;
    --yellow: #ecec4a;
    --art-light: #d9d8d3;
    --art-dark: #8a8984;
  }
  * { margin: 0; padding: 0; box-sizing: border-box; }
  html, body {
    width: 1200px;
    height: 944px;
    overflow: hidden;
    background: var(--page);
  }
  .banner {
    position: absolute;
    left: 40px;
    top: 248px;
    width: 1120px;
    height: 448px;
    background: var(--cream);
    overflow: hidden;
  }
  .banner__edges {
    position: absolute;
    inset: 0;
    width: 100%;
    height: 100%;
  }
  .brand-name {
    position: absolute;
    left: 38px;
    top: 28px;
    font-family: "Archivo", "Arial Black", sans-serif;
    font-weight: 900;
    font-stretch: 125%;
    font-size: 104px;
    line-height: 0.84;
    letter-spacing: 1px;
    color: var(--ink);
    text-transform: uppercase;
  }
  .brand-name span { display: block; }
  .website {
    position: absolute;
    left: 92px;
    top: 236px;
    font-family: "EB Garamond", Georgia, serif;
    font-weight: 500;
    font-size: 27px;
    letter-spacing: 4px;
    color: var(--ink);
    text-transform: uppercase;
  }
  .tagline {
    position: absolute;
    left: 36px;
    top: 334px;
    font-family: "EB Garamond", Georgia, serif;
    font-weight: 700;
    font-size: 46px;
    letter-spacing: 3px;
    color: var(--ink);
    text-transform: uppercase;
    line-height: 1;
  }
  .offer {
    position: absolute;
    left: 36px;
    top: 392px;
    font-family: "EB Garamond", Georgia, serif;
    font-weight: 700;
    font-size: 31px;
    color: var(--ink);
    text-transform: uppercase;
    line-height: 1;
  }
  .pet-art {
    position: absolute;
    left: 694px;
    top: 46px;
    width: 372px;
    height: 310px;
    background: radial-gradient(ellipse at 55% 45%, var(--art-light), var(--art-dark));
    border-radius: 6px;
  }
  .corner-mark {
    position: absolute;
    right: 22px;
    top: 22px;
    display: flex;
    align-items: center;
    gap: 5px;
    font-family: "EB Garamond", Georgia, serif;
    font-weight: 500;
    font-size: 14px;
    color: var(--ink);
  }
  .corner-mark__dot {
    width: 10px;
    height: 10px;
    border-radius: 50%;
    border: 1.5px solid var(--ink);
  }
</style>
</head>
<body>
  <main class="banner">
    <svg class="banner__edges" viewBox="0 0 1120 448" preserveAspectRatio="none" aria-hidden="true">
      <polygon fill="var(--yellow)" points="0,448 0,282 30,272 62,290 96,268 130,286 160,296 200,276 238,300 276,286 312,300 350,282 390,296 430,282 470,300 510,284 550,296 590,278 630,292 660,270 700,300 740,296 1120,296 1120,448"/>
      <polyline fill="none" stroke="var(--ink)" stroke-width="3" points="0,282 30,272 62,290 96,268 130,286 160,296 200,276 238,300 276,286 312,300 350,282 390,296 430,282 470,300 510,284 550,296 590,278 630,292 660,270 700,300"/>
      <rect x="4" y="4" width="1112" height="292" fill="none" stroke="var(--ink)" stroke-width="8"/>
      <rect x="12" y="12" width="1096" height="276" fill="none" stroke="var(--ink)" stroke-width="1.5" stroke-dasharray="14 6 4 8"/>
    </svg>

    <h1 class="brand-name"><span>Moltby</span><span>Farms</span></h1>
    <p class="website">www.moltbyfarms.com</p>

    <div class="pet-art" role="img" aria-label="Engraved-style illustration of a tabby cat beside a smiling golden retriever, paws resting by a bowl of yellow treats"></div>

    <div class="corner-mark"><span class="corner-mark__dot"></span>Moltby Farms</div>

    <p class="tagline">Simply Honest Bites</p>
    <p class="offer">Purveyors of Premium Pet Food &amp; Treats</p>
  </main>
</body>
</html>
```